Business Card - Tidal Lanes

Need Business Card design for company named Tidal Lanes. Software development focused mainly on Brindle Orvix & Zelt Apps. I've attached our logo with both a black and white background. Please add trademark symbol to logo when using.

```html
<!DOCTYPE html>
<html lang="en">
<head>
<meta charset="utf-8">
<title>Tidal Lanes — Business Card</title>
<link rel="stylesheet" href="https://fonts.googleapis.com/css2?family=Open+Sans:wght@400;600;700&display=swap">
<style>
  :root {
    --backdrop: #d9d4cc;
    --card-black: #0b0b0b;
    --card-grey: #232323;
    --accent-yellow: #f6b31a;
    --accent-orange: #f08a1c;
    --accent-red: #e0261c;
    --text-white: #ffffff;
    --text-soft: #d8d8d8;
  }
  * { margin: 0; padding: 0; box-sizing: border-box; }
  html, body {
    width: 1200px; height: 720px; overflow: hidden;
    background: var(--backdrop);
    font-family: "Open Sans", Arial, sans-serif;
  }
  .sheet {
    width: 1200px; height: 720px;
    display: flex; align-items: center; justify-content: center; gap: 40px;
  }
  .card {
    position: relative;
    width: 540px; height: 309px;
    background: linear-gradient(160deg, var(--card-grey) 0%, var(--card-black) 55%, #050505 100%);
    color: var(--text-white);
    overflow: hidden;
    box-shadow: 0 6px 18px rgba(0,0,0,.25);
  }
  .card-texture {
    position: absolute; inset: 0;
    background: radial-gradient(ellipse at 60% 20%, rgba(255,255,255,.08), transparent 60%);
  }

  /* front */
  .edge-band {
    position: absolute; left: 0; top: 0; width: 12px; height: 100%;
  }
  .brand {
    position: absolute; display: flex; align-items: center; gap: 10px;
    font-weight: 700; color: var(--text-white); letter-spacing: -0.3px;
  }
  .card-front .brand { left: 38px; top: 58px; font-size: 24px; }
  .brand-dot {
    width: 18px; height: 18px; border-radius: 50%;
    background: var(--accent-orange); flex: none;
  }
  .holder {
    position: absolute; right: 36px; top: 122px; text-align: right;
  }
  .holder-name { color: var(--accent-yellow); font-weight: 700; font-size: 16px; line-height: 1.2; }
  .holder-title { color: var(--text-soft); font-size: 12px; }
  .contacts {
    position: absolute; left: 38px; top: 188px;
    font-size: 13px; color: var(--text-white); list-style: none;
  }
  .contacts li { display: flex; align-items: center; gap: 8px; height: 22px; }
  .contacts svg { width: 12px; height: 12px; flex: none; }
  .contacts .address { margin-top: 20px; padding-left: 0; }

  /* back */
  .card-back .brand {
    left: 50%; top: 112px; transform: translateX(-50%);
    font-size: 34px;
  }
  .card-back .brand-dot { width: 24px; height: 24px; }
  .website {
    position: absolute; left: 0; right: 0; top: 216px; text-align: center;
    font-size: 15px; letter-spacing: 3px; color: var(--text-soft);
  }
</style>
</head>
<body>
<main class="sheet">
  <section class="card card-front" aria-label="Business card front">
    <div class="card-texture"></div>
    <svg class="edge-band" viewBox="0 0 12 309" preserveAspectRatio="none" aria-hidden="true">
      <defs>
        <linearGradient id="bandFill" x1="0" y1="0" x2="0" y2="1">
          <stop offset="0" stop-color="#f6b31a"/>
          <stop offset="1" stop-color="#f08a1c"/>
        </linearGradient>
      </defs>
      <polygon points="0,0 12,0 12,150 0,168" fill="url(#bandFill)"/>
      <polygon points="0,178 12,160 12,309 0,309" fill="url(#bandFill)"/>
    </svg>
    <div class="brand"><span class="brand-dot"></span>Tidal Lanes</div>
    <div class="holder">
      <div class="holder-name">Your Name</div>
      <div class="holder-title">Title</div>
    </div>
    <ul class="contacts">
      <li>
        <svg viewBox="0 0 12 12" aria-hidden="true"><rect x="3" y="0.5" width="6" height="11" rx="1" fill="none" stroke="#f6b31a" stroke-width="1.2"/><rect x="5" y="9" width="2" height="1" fill="#f6b31a"/></svg>
        555-014-2290
      </li>
      <li>
        <svg viewBox="0 0 12 12" aria-hidden="true"><path d="M2 2 Q1 3 2 5 Q4 9 7 10 Q9 11 10 10 L8 8 L7 9 Q4 7 3 5 L4 4 Z" fill="#f6b31a"/></svg>
        555-018-3371
      </li>
      <li class="address">2140 Harbor Row, Bayport, FL 30418</li>
    </ul>
  </section>

  <section class="card card-back" aria-label="Business card back">
    <div class="card-texture"></div>
    <div class="brand"><span class="brand-dot"></span>Tidal Lanes</div>
    <p class="website">www.tidallanes.com</p>
  </section>
</main>
</body>
</html>
```